Book cover

I need a cover for a my 3rd book that kinda goes with my brand (my previous book. The name of my first book - "Turbulence Behind the Yoke" Hidden Strain Inside Modern Cockpits: A Guide for Travelers". In the same style I need my third book - NO HARBOR" to stand out. I need a bolder, less whimsy cover, less playful. So can we use some of the same elements to stay consistent in this book cover. Perhaps use text to envoke emotions. This is the back cover so far (see below attachemnent)

Hello,
Subject: Cover Direction & Brand Consistency

Hi everyone,

Here’s my honest take: I don’t think the current execution fully reflects my brand yet. What I’m wondering is whether we can bring more continuity across my books—borrowing elements from my first and second covers to inform this third one. Think of how authors like Dorian Welk maintain a recognizable style across their work. That consistency builds trust and signals authority before a reader even opens the book. Design choices like this matter more than we realize.

I’ve attached a cover I came across on Brindlemart that reminded me of Option 5 and feels aligned with where you’re headed. One thought: could we experiment with introducing a crack—or cracks—into the word HARBOR itself? Maybe put the title "NO HARBOR" at the edge of the cover vertically?

Curious to hear your thoughts and how you see this evolving.
P.s. Is there away to attach an idea?

NO HARBOR: Restoring Quiet Edges in a Culture that Praises Hurry

```html
<!DOCTYPE html>
<html lang="en">
<head>
<meta charset="utf-8">
<title>No Harbor — Book Cover</title>
<link rel="stylesheet" href="https://fonts.googleapis.com/css2?family=Oswald:wght@600&family=Roboto:wght@500&family=Montserrat:wght@700&display=swap">
<style>
  :root {
    --page-bg: #ffffff;
    --cover-night: #0b1320;
    --sky-deep: #1d3357;
    --sky-light: #8fb0cf;
    --horizon: #d9dde0;
    --runway: #6d6a66;
    --runway-dark: #1c1c1f;
    --title-white: #ffffff;
    --accent-blue: #1ea7e8;
  }
  * { margin: 0; padding: 0; box-sizing: border-box; }
  html, body {
    width: 1200px; height: 1200px; overflow: hidden;
    background: var(--page-bg);
  }
  .book-cover {
    position: absolute; left: 308px; top: 160px;
    width: 594px; height: 888px; overflow: hidden;
    background: var(--cover-night);
  }
  .cover-photo {
    position: absolute; inset: 0;
    background: linear-gradient(180deg,
      var(--cover-night) 0%,
      var(--sky-deep) 18%,
      var(--sky-light) 36%,
      var(--horizon) 44%,
      var(--runway) 56%,
      var(--runway) 72%,
      var(--runway-dark) 92%,
      var(--cover-night) 100%);
  }
  .title-rule {
    position: absolute; left: 211px; top: 464px;
    width: 341px; height: 2px; background: var(--title-white);
  }
  .title-no, .title-harbor {
    position: absolute; left: 52px;
    font-family: "Oswald", "Arial Narrow", sans-serif;
    font-weight: 600; font-size: 134px; color: var(--title-white);
    line-height: 1; text-transform: uppercase; white-space: nowrap;
  }
  .title-no { top: 449px; letter-spacing: -2px; }
  .title-harbor { top: 583px; letter-spacing: 0; }
  .subtitle {
    position: absolute; left: 211px; top: 474px;
    font-family: "Roboto", Arial, sans-serif; font-weight: 500;
    font-size: 29px; line-height: 33px; color: var(--title-white);
    text-transform: uppercase; white-space: nowrap;
  }
  .subtitle-accent { color: var(--accent-blue); }
  .author {
    position: absolute; left: 0; right: 0; top: 814px;
    text-align: center;
    font-family: "Montserrat", Arial, sans-serif; font-weight: 700;
    font-size: 23px; letter-spacing: 2px; color: var(--accent-blue);
    text-transform: uppercase;
  }
</style>
</head>
<body>
  <main class="book-cover">
    <div class="cover-photo" role="img" aria-label="Low-angle photograph of an airliner's landing gear on a cracked runway with a yellow centre line under a dusky blue sky"></div>

    <div class="title-rule"></div>
    <h1>
      <span class="title-no">No</span>
      <span class="title-harbor">Harbor</span>
    </h1>
    <p class="subtitle">
      Restoring quiet<br>
      edges in a culture<br>
      <span class="subtitle-accent">that praises hurry</span>
    </p>

    <p class="author">Capt. Marlo Quintrell</p>
  </main>
</body>
</html>
```